Dietitian needs awesome business card

I need a contemporary design that's eye catching but professional.
My card is to given to doctors, specialists and patients alike.
I manage patients with chronic diseases
I have uploaded my logo and current business card, I would also like the other Certified Clinical Nutritionist logo incorporated into the design

Target Market(s)

Doctors, specialists and patients

Industry/Entity Type

Healthcare

Contact Information for Business Card

www.brightfieldnutrition.com.au
Ph: 0427 561 903
Fax: 6457 2183
email: marcus.k.diet@fernmail.com
Space on the back of the card with: Appointment date, Appointment time and appointment location

Font styles to use
Serif

Colors
fbee3e
876aae
ffc214

Requirements
Must have
• My Logo
• Certified Clinical Nutritionist Logo
• My 4 locations - Pinebrook Medical Centre, North Corrin Health, Hollis Medical, Ashcombe Doctors Surgery
Nice to have
• I like the colours in my current business card

```html
<!DOCTYPE html>
<html lang="en">
<head>
<meta charset="utf-8">
<title>Brightfield Nutrition &amp; Dietetics – Business Card</title>
<link rel="stylesheet" href="https://fonts.googleapis.com/css2?family=Arimo:wght@400;700&display=swap">
<style>
  :root {
    --stage: #2e2e30;
    --card: #ffffff;
    --navy: #1b2a8f;
    --navy-deep: #14207a;
    --blue-mid: #0b63b8;
    --green: #7bbf2a;
    --green-deep: #2a9a3a;
    --orange: #f26b1d;
    --grey-text: #4a4a4a;
    --rule: #c9cdd2;
  }
  * { box-sizing: border-box; margin: 0; padding: 0; }
  html, body { width: 1200px; height: 987px; overflow: hidden; }
  body {
    background: var(--stage);
    font-family: "Arimo", Arial, sans-serif;
    position: relative;
  }
  .card {
    position: absolute;
    left: 293px;
    width: 615px;
    height: 350px;
    border-radius: 20px;
    overflow: hidden;
    background: var(--card);
  }
  .card--front { top: 129px; }
  .card--back { top: 507px; }

  /* Front */
  .brand {
    position: absolute;
    left: 36px; top: 112px;
    display: flex; align-items: center; gap: 10px;
  }
  .brand__dot {
    width: 46px; height: 46px; border-radius: 50%;
    background: var(--navy);
  }
  .brand__name {
    color: var(--navy);
    font-size: 17px;
    font-weight: 400;
    line-height: 1.25;
  }
  .divider {
    position: absolute;
    left: 289px; top: 73px;
    width: 1px; height: 147px;
    background: var(--rule);
  }
  .person { position: absolute; left: 313px; top: 70px; }
  .person__name { color: var(--navy); font-size: 22px; font-weight: 700; }
  .person__title { color: var(--orange); font-size: 16.5px; margin-top: 5px; }
  .person__role { color: var(--green); font-size: 16.5px; margin-top: 3px; }
  .contacts { position: absolute; left: 313px; top: 152px; list-style: none; }
  .contacts li {
    display: flex; align-items: center; gap: 10px;
    color: var(--grey-text); font-size: 16.5px; height: 24px;
  }
  .contacts svg { width: 15px; height: 15px; fill: var(--navy); flex: none; }
  .wave { position: absolute; left: 0; top: 0; width: 615px; height: 350px; }
  .website {
    position: absolute; left: 0; right: 0; top: 315px;
    text-align: center; color: #fff;
    font-size: 16px; font-weight: 700; letter-spacing: 2.4px;
  }

  /* Back */
  .backdrop {
    position: absolute; inset: 0;
    background: radial-gradient(ellipse at 40% 60%, #eef3e6 0%, #f6f8f2 45%, #ffffff 85%);
  }
  .appointment__title {
    position: absolute; left: 0; right: 0; top: 30px;
    text-align: center; color: var(--navy-deep);
    font-size: 21px; font-weight: 700;
  }
  .appointment__line {
    position: absolute; left: 42px; width: 530px; height: 1px;
    background: var(--rule);
  }
  .when {
    position: absolute; left: 42px; top: 224px;
    color: var(--navy-deep); font-size: 16.5px; white-space: nowrap;
  }
  .when .dots { color: var(--navy-deep); letter-spacing: 0.5px; font-size: 13px; }
  .when small { font-size: 13px; }
  .locations {
    position: absolute; left: 42px; top: 266px;
    list-style: none;
    display: grid; grid-template-columns: 306px auto; row-gap: 5px;
  }
  .locations li {
    display: flex; align-items: center; gap: 7px;
    color: var(--grey-text); font-size: 16.5px;
  }
  .locations li::before {
    content: ""; width: 12px; height: 12px;
    border: 1.5px solid var(--navy);
  }
</style>
</head>
<body>

<section class="card card--front">
  <div class="brand">
    <span class="brand__dot"></span>
    <span class="brand__name">Brightfield<br>Nutrition &amp; Dietetics</span>
  </div>
  <div class="divider"></div>
  <div class="person">
    <h1 class="person__name">Marcus Kellaway</h1>
    <p class="person__title">Certified Clinical Nutritionist</p>
    <p class="person__role">Nutritionist &amp; Chef</p>
  </div>
  <ul class="contacts">
    <li><svg viewBox="0 0 24 24"><path d="M6.6 10.8a15.1 15.1 0 0 0 6.6 6.6l2.2-2.2c.3-.3.7-.4 1-.2 1.1.4 2.3.6 3.6.6.6 0 1 .4 1 1V20c0 .6-.4 1-1 1A17 17 0 0 1 3 4c0-.6.4-1 1-1h3.5c.6 0 1 .4 1 1 0 1.3.2 2.5.6 3.6.1.3 0 .7-.2 1z"/></svg>0427 561 903</li>
    <li><svg viewBox="0 0 24 24"><path d="M7 3h10v5H7zM4 9h16a2 2 0 0 1 2 2v6h-4v4H6v-4H2v-6a2 2 0 0 1 2-2zm4 7v3h8v-3z"/></svg>6457 2183</li>
    <li><svg viewBox="0 0 24 24"><path d="M3 5h18v14H3zm2 2v.5l7 5 7-5V7l-7 5z"/></svg>marcus.k.diet@fernmail.com</li>
  </ul>
  <svg class="wave" viewBox="0 0 615 350" aria-hidden="true">
    <defs>
      <linearGradient id="band-blue" x1="0" x2="1" y1="0" y2="0">
        <stop offset="0" stop-color="#16238a"/>
        <stop offset="0.55" stop-color="#0b5cb3"/>
        <stop offset="1" stop-color="#14207a"/>
      </linearGradient>
      <linearGradient id="band-green" x1="0" x2="1">
        <stop offset="0" stop-color="#2a9a3a"/>
        <stop offset="0.6" stop-color="#9fd12e"/>
        <stop offset="1" stop-color="#ffffff"/>
      </linearGradient>
    </defs>
    <path d="M0 252 C150 282 300 302 480 298 C300 316 130 300 0 276 Z" fill="url(#band-green)"/>
    <path d="M60 258 C250 300 430 300 615 258 L615 272 C430 310 250 312 60 258 Z" fill="#1d5fb8"/>
    <path d="M0 278 C160 304 330 320 615 265 L615 350 L0 350 Z" fill="url(#band-blue)"/>
  </svg>
  <p class="website">WWW.BRIGHTFIELDNUTRITION.COM.AU</p>
</section>

<section class="card card--back">
  <div class="backdrop" role="img" aria-label="Faint photograph of fresh green vegetables"></div>
  <h2 class="appointment__title">YOUR APPOINTMENT</h2>
  <div class="appointment__line" style="top:84px"></div>
  <div class="appointment__line" style="top:119px"></div>
  <div class="appointment__line" style="top:154px"></div>
  <div class="appointment__line" style="top:189px"></div>
  <p class="when">Date : <span class="dots">&nbsp;.............................................</span> Time : <span class="dots">..............................</span> <small>AM/PM</small></p>
  <ul class="locations">
    <li>Pinebrook Medical Centre</li>
    <li>Hollis Medical</li>
    <li>North Corrin Health</li>
    <li>Ashcombe Doctors Surgery</li>
  </ul>
</section>

</body>
</html>
```